Telecommunications/Power civil contractor needs business card design

Were a new telecommunications/power underground civil contractor that is looking for a new business card design. Our company colours are silver or grey and orange. Feel free to use the white background logo or the black background logo.

Target Market(s)

Local contractors, utility companies, private sector mining/energy companies, developers.

Industry/Entity Type

Telecommunications

Contact Information for Business Card

Each card will need the following info:
Persons name:
Title:
E-mail:
Phone number:
Shop Address:
Mailing Address:

Requirements
Must have
• Each card will need the following info:
• Persons name:
• Title:
• E-mail:
• Phone number:
• Shop Address:
• Mailing Address:

```html
<!DOCTYPE html>
<html lang="en">
<head>
<meta charset="utf-8">
<title>Dig Line Contracting Inc — Business Card</title>
<link rel="stylesheet" href="https://fonts.googleapis.com/css2?family=Open+Sans:wght@400;600;700;800&display=swap">
<style>
  :root {
    --orange: #f05a22;
    --grey: #7a7a7a;
    --grey-dark: #5c5c5c;
    --grey-light: #b5b5b5;
    --ink: #3a3a3a;
    --black: #0b0b0b;
    --white: #ffffff;
    --backdrop: #2b2b2b;
  }
  * { box-sizing: border-box; margin: 0; padding: 0; }
  html, body {
    width: 1200px; height: 900px; overflow: hidden;
    background: var(--backdrop);
    font-family: "Open Sans", Arial, sans-serif;
  }
  .canvas { position: relative; width: 1200px; height: 900px; }

  .card {
    position: absolute;
    width: 600px; height: 342px;
    overflow: hidden;
    box-shadow: 0 14px 30px rgba(0,0,0,.45);
  }

  /* Front: black card */
  .card-front { left: 70px; top: 70px; background: var(--black); }
  .card-front .brand {
    position: absolute; left: 0; right: 0; top: 92px;
    display: flex; flex-direction: column; align-items: center; gap: 16px;
  }

  .brand-mark {
    width: 74px; height: 74px; border-radius: 50%;
    border: 5px solid var(--orange);
  }
  .brand-name {
    font-weight: 800; color: var(--orange);
    text-transform: uppercase; text-align: center;
    line-height: 1.05; letter-spacing: 1px;
  }
  .card-front .brand-name { font-size: 24px; }

  /* Back: contact card */
  .card-back { left: 530px; top: 488px; background: var(--white); }
  .card-back .shapes { position: absolute; inset: 0; }
  .card-back .brand {
    position: absolute; left: 0; width: 290px; top: 96px;
    display: flex; flex-direction: column; align-items: center; gap: 16px;
  }
  .card-back .brand-name { font-size: 26px; }

  .name-band {
    position: absolute; left: 350px; top: 36px;
  }
  .person-name {
    font-weight: 700; font-size: 19px; color: var(--orange);
    text-transform: uppercase; letter-spacing: .3px;
  }
  .person-title { font-size: 13px; color: var(--ink); margin-top: 1px; }

  .contact-list { position: absolute; left: 0; top: 0; width: 600px; height: 342px; list-style: none; }
  .contact-item {
    position: absolute; left: 352px;
    font-size: 14.5px; color: var(--white); line-height: 1.3;
  }
  .contact-item.address { top: 178px; }
  .contact-item.phone { top: 232px; font-size: 16px; }
  .contact-item.email { top: 272px; }
</style>
</head>
<body>
<main class="canvas">

  <section class="card card-front" aria-label="Business card front">
    <div class="brand">
      <span class="brand-mark" aria-hidden="true"></span>
      <p class="brand-name">Dig Line<br>Contracting Inc</p>
    </div>
  </section>

  <section class="card card-back" aria-label="Business card back">
    <svg class="shapes" width="600" height="342" viewBox="0 0 600 342" aria-hidden="true">
      <rect x="300" y="0" width="300" height="342" fill="#f05a22"/>
      <polygon points="278,0 318,0 318,342 298,342" fill="#7a7a7a"/>
      <polygon points="298,0 336,0 336,100 318,118 318,342 300,342" fill="#5c5c5c"/>
      <polygon points="324,28 600,28 600,96 324,96 336,62" fill="#ffffff"/>
      <polygon points="340,52 352,62 340,72" fill="#f05a22"/>
      <!-- icon hexagons -->
      <g fill="#f05a22">
        <polygon points="308,178 320,185 320,199 308,206 296,199 296,185"/>
        <polygon points="308,228 320,235 320,249 308,256 296,249 296,235"/>
        <polygon points="308,268 320,275 320,289 308,296 296,289 296,275"/>
      </g>
      <!-- pin -->
      <path d="M308 185 a6 6 0 0 1 6 6 c0 4 -6 9 -6 9 s-6 -5 -6 -9 a6 6 0 0 1 6 -6z" fill="#ffffff"/>
      <circle cx="308" cy="191" r="2.2" fill="#f05a22"/>
      <!-- phone -->
      <path d="M302 236 h4 l1 4 -2 1.5 a9 9 0 0 0 4 4 l1.5 -2 4 1 v4 a11 11 0 0 1 -12.5 -12.5z" fill="#ffffff"/>
      <!-- mail -->
      <rect x="301" y="277" width="14" height="10" fill="#ffffff"/>
      <polyline points="301,277 308,283 315,277" fill="none" stroke="#f05a22" stroke-width="1.4"/>
    </svg>

    <div class="brand">
      <span class="brand-mark" aria-hidden="true"></span>
      <p class="brand-name">Dig Line<br>Contracting Inc</p>
    </div>

    <div class="name-band">
      <p class="person-name">Morgan Hale</p>
      <p class="person-title">Managing Director</p>
    </div>

    <ul class="contact-list">
      <li class="contact-item address">N. 12 Sample Road,<br>Suite 200, Fairview, WA 55555</li>
      <li class="contact-item phone">555.010.2020</li>
      <li class="contact-item email">info@diglinecontracting.com</li>
    </ul>
  </section>

</main>
</body>
</html>
```